Business cards in digital learning for freelancer

Hello, I need a business cards in french. I work in the Digital learning industries as freeelancer; I'm an expert in digital learning. I work in France. My customer are in the health industry, pharmaceutical industry, and training organization. I've got a logo. I offer three services: consulting, Design, and Training. In the consulting, I offers coaching to choose your digital learning tools and the digital learning strategy. For the Design, I product differents level of elearning like rapid-learning, elearning, micro-learning, video-learning. And for the training service, I've create training about pedagogy, digital learning management project, Digital learning design.
I join my Logo create in this platform. My universe is gamified. I like the life, and I'm very social. I want a card like I'm I. I love Art (painting), Europeen comics. I use in my visual support "permanent maker" font and caracters. I would like cards: elegant, modern, Top class. If you need any information, you can ask me.
thanks for ideas

Target Market(s)

in health industries and training organization for Training manager, instructor, human resources director

Contact Information for Business Card

Phone number : 06 71 38 95 14 , mail: bastiengolmier@quelmoto.fr, web: bastiengolmier.fr , Carrivo

Font styles to use
Sans Serif

Requirements
Must have
• Use my logo and write my 3 services (consulting, training, design)

```html
<!DOCTYPE html>
<html lang="fr">
<head>
<meta charset="utf-8">
<title>Golmier — Cartes de visite</title>
<link rel="stylesheet" href="https://fonts.googleapis.com/css2?family=Cinzel:wght@500&family=Montserrat:wght@400;500;800&display=swap">
<style>
  :root {
    --backdrop: #1f1f1f;
    --orange: #f37324;
    --paper: #ffffff;
    --ink: #5a5a5a;
    --rule: #8a8a8a;
    --rule-light: rgba(255,255,255,0.55);
  }
  * { box-sizing: border-box; margin: 0; padding: 0; }
  html, body {
    width: 1200px; height: 1040px; overflow: hidden;
    background: var(--backdrop);
    font-family: "Montserrat", Arial, sans-serif;
  }
  .canvas { position: relative; width: 1200px; height: 1040px; }

  .card {
    position: absolute; left: 270px; width: 660px; height: 360px;
  }

  /* Front (orange) */
  .card-front {
    top: 130px;
    background: var(--orange);
    border-radius: 80px 0 80px 0;
    color: var(--paper);
    display: flex; flex-direction: column; align-items: center; justify-content: center;
  }
  .brand-name {
    display: flex; align-items: center; gap: 14px;
    font-weight: 800; font-size: 64px; letter-spacing: 4px; line-height: 1;
  }
  .brand-dot { width: 18px; height: 18px; border-radius: 50%; background: currentColor; }
  .brand-field {
    margin-top: 10px; font-size: 15px; letter-spacing: 5px; text-transform: uppercase; font-weight: 400;
  }
  .services {
    margin-top: 22px; font-size: 14px; letter-spacing: 2.5px; font-weight: 500;
    display: flex; align-items: center; gap: 12px;
  }
  .services .bullet { width: 8px; height: 8px; border-radius: 50%; background: var(--paper); }
  .social {
    margin-top: 44px; display: flex; align-items: center; gap: 14px; font-size: 13px; font-weight: 500;
  }
  .social .line { width: 150px; height: 1px; background: var(--rule-light); }
  .social .mark { display: flex; align-items: center; gap: 7px; }
  .social .circle { width: 14px; height: 14px; border-radius: 50%; background: var(--paper); }

  /* Back (white) */
  .card-back {
    top: 550px;
    background: var(--paper);
    border-radius: 0 80px 0 80px;
    display: flex; align-items: center;
  }
  .back-brand {
    width: 330px; display: flex; flex-direction: column; align-items: center; color: var(--orange);
  }
  .back-brand .brand-name { font-size: 46px; letter-spacing: 3px; }
  .back-brand .brand-dot { width: 14px; height: 14px; }
  .back-brand .brand-field { color: var(--ink); font-size: 12px; letter-spacing: 4px; }
  .divider { width: 1px; height: 200px; background: var(--rule); }
  .contact { padding-left: 38px; }
  .person-name {
    font-family: "Cinzel", Georgia, serif; color: var(--orange); font-size: 26px; letter-spacing: 1.5px;
  }
  .person-role { color: var(--ink); font-size: 17px; margin-top: 2px; }
  .contact-list { list-style: none; margin-top: 22px; color: var(--ink); font-size: 16px; }
  .contact-list li { display: flex; align-items: center; gap: 10px; margin-bottom: 6px; }
  .contact-list svg { width: 16px; height: 16px; flex: none; }
</style>
</head>
<body>
<main class="canvas">
  <section class="card card-front">
    <div class="brand-name"><span>GOLMIER</span><span class="brand-dot"></span></div>
    <p class="brand-field">Digital Learning</p>
    <p class="services">CONSULTING <span class="bullet"></span> TRAINING <span class="bullet"></span> DESIGN</p>
    <div class="social">
      <span class="line"></span>
      <span class="mark"><span class="circle"></span>Carrivo</span>
      <span class="line"></span>
    </div>
  </section>

  <section class="card card-back">
    <div class="back-brand">
      <div class="brand-name"><span>GOLMIER</span><span class="brand-dot"></span></div>
      <p class="brand-field">Digital Learning</p>
    </div>
    <span class="divider"></span>
    <div class="contact">
      <h1 class="person-name">Lucien Marchal</h1>
      <p class="person-role">Managing Director</p>
      <ul class="contact-list">
        <li>
          <svg viewBox="0 0 24 24" aria-hidden="true"><path fill="#f37324" d="M6.6 10.8a15 15 0 0 0 6.6 6.6l2.2-2.2c.3-.3.7-.4 1-.2 1.1.4 2.3.6 3.6.6.6 0 1 .4 1 1V20c0 .6-.4 1-1 1A17 17 0 0 1 3 4c0-.6.4-1 1-1h3.5c.6 0 1 .4 1 1 0 1.3.2 2.5.6 3.6.1.3 0 .7-.2 1z"/></svg>
          06 71 38 95 14
        </li>
        <li>
          <svg viewBox="0 0 24 24" aria-hidden="true"><rect x="2" y="5" width="20" height="14" fill="#f37324"/><path d="M2 5l10 8 10-8" fill="none" stroke="#fff" stroke-width="1.6"/></svg>
          bastiengolmier@quelmoto.fr
        </li>
        <li>
          <svg viewBox="0 0 24 24" aria-hidden="true"><g fill="none" stroke="#f37324" stroke-width="1.8"><circle cx="12" cy="12" r="9"/><ellipse cx="12" cy="12" rx="4" ry="9"/><path d="M3 12h18M5 7h14M5 17h14"/></g></svg>
          www.bastiengolmier.fr
        </li>
      </ul>
    </div>
  </section>
</main>
</body>
</html>
```